new service company in the field of construction seeks to make the Creation of a PPT

We need a PPT format with a cover page a frame for presentation. our company is based in Paris which was named VORENTIX. we just did our logo attached. Our company offers services to manage and control documents that pass on projects in construction (building, infrastructure, energy, oil and gas etc. ..). We use internet systems to help us, design must show insurance, quality, and safety. Customers should build any type of works and can not build without the approved documents. These documents go through multiple validations, and vorentix staff seconded on projects, coordinate these processes and documents, quality documents, to ensure that project deadlines are met and project management sees his project developed within the period, through regular reporting. the services offered by our company help ensure the project of building on time, to ensure the project manager visibility on what e will not, and can act accordingly.

Target Market(s)

general contractor of engineering construction or big business masters lumber wholesale real estate investor, project ownership in the construction sector

Industry/Entity Type

Construction

Contact Information for Business Card

carte rectangulaire petite taille (4X6cm env)
horizontale ou verticale
prendre en compte les éléments suivants :
logo
nom de société
adresse postale (4 lignes)
teléphone:
mail
role (ex : directeur)
in the back : La qualité documentaire de vos projets

Font styles to use
Sans Serif

Colors
34a7d7
85cae6
cee9f5
0592cd

Requirements
Must have
• The project should have 2 sliders: slider 1. Cover Page 2. slider for the content of presentations THE GOAL IS TO HAVE A VISUAL IDENTITY ON PPT, MY BUSINESS CARDS AND LETTERS must stay in mind and colors of the logo that joined the design must be clean and recall the seriousness, ease. the design must take into account the page numbers Tag line: the documentary quality of your projects information such as tagline and writes must be modifiable
Nice to have
• would require the presentation of the figure shows concepts or reporting table THE GOAL IS TO HAVE A VISUAL IDENTITY ON PPT, MY BUSINESS CARDS AND LETTERS
Should not have
• not to building or building in the logo

```html
<!DOCTYPE html>
<html lang="en">
<head>
<meta charset="utf-8">
<title>VORENTIX – How it works</title>
<link rel="stylesheet" href="https://fonts.googleapis.com/css2?family=Open+Sans:wght@400;600;700&display=swap">
<style>
  :root {
    --bg: #ffffff;
    --band-light: #9fd3d6;
    --band-mid: #5bb0cf;
    --band-deep: #1f78b8;
    --step-1: #2379b8;
    --step-2: #3a98c8;
    --step-3: #5ab0c7;
    --step-4: #8ccbc6;
    --connector: #4a4a4a;
    --body-text: #444444;
    --title-text: #ffffff;
    --brand: #2d6fb5;
  }
  html, body {
    margin: 0;
    padding: 0;
    width: 1200px;
    height: 662px;
    overflow: hidden;
    background: var(--bg);
  }
  .slide {
    display: block;
    width: 1200px;
    height: 662px;
    font-family: "Open Sans", Arial, sans-serif;
  }
  .slide-title {
    fill: var(--title-text);
    font-weight: 700;
    font-size: 40px;
  }
  .step-circle--1 { fill: var(--step-1); }
  .step-circle--2 { fill: var(--step-2); }
  .step-circle--3 { fill: var(--step-3); }
  .step-circle--4 { fill: var(--step-4); }
  .step-number {
    fill: #ffffff;
    font-weight: 700;
  }
  .connector {
    stroke: var(--connector);
    stroke-width: 14;
  }
  .step-text {
    fill: var(--body-text);
    font-size: 15px;
  }
  .brand-name {
    fill: var(--brand);
    font-weight: 600;
    font-size: 30px;
    letter-spacing: 1px;
  }
  .brand-dot { fill: var(--brand); }
</style>
</head>
<body>
<svg class="slide" viewBox="0 0 1024 565" xmlns="http://www.w3.org/2000/svg">
  <defs>
    <linearGradient id="header-band-fill" x1="0" y1="0" x2="1" y2="0">
      <stop offset="0" stop-color="var(--band-light)"/>
      <stop offset="0.55" stop-color="var(--band-mid)"/>
      <stop offset="1" stop-color="var(--band-deep)"/>
    </linearGradient>
  </defs>

  <g class="header-band" role="img" aria-label="Decorative low-poly header band in teal and blue tones">
    <polygon fill="url(#header-band-fill)"
      points="0,0 1024,0 1024,130 985,168 860,125 740,72 650,138 360,95 230,80 0,130"/>
  </g>

  <text class="slide-title" x="528" y="60" text-anchor="middle">HOW IT WORKS</text>

  <g class="connectors">
    <line class="connector" x1="264" y1="298" x2="330" y2="340"/>
    <line class="connector" x1="507" y1="340" x2="577" y2="293"/>
    <line class="connector" x1="702" y1="293" x2="778" y2="343"/>
  </g>

  <g class="step step--1">
    <circle class="step-circle--1" cx="209" cy="259" r="50"/>
    <text class="step-number" x="209" y="273" font-size="38" text-anchor="middle">01</text>
    <text class="step-text" text-anchor="middle">
      <tspan x="158" y="352">Lorem ipsum dolor sit amet,</tspan>
      <tspan x="158" y="371">consectetur adipiscing elit, sed</tspan>
      <tspan x="158" y="390">do eiusmod tempor</tspan>
    </text>
  </g>

  <g class="step step--2">
    <circle class="step-circle--2" cx="418" cy="402" r="92"/>
    <text class="step-number" x="418" y="430" font-size="78" text-anchor="middle">02</text>
    <text class="step-text" text-anchor="middle">
      <tspan x="418" y="221">Lorem ipsum dolor sit amet,</tspan>
      <tspan x="418" y="240">consectetur adipiscing elit,</tspan>
      <tspan x="418" y="259">sed do eiusmod tempor</tspan>
    </text>
  </g>

  <g class="step step--3">
    <circle class="step-circle--3" cx="641" cy="249" r="60"/>
    <text class="step-number" x="641" y="267" font-size="50" text-anchor="middle">03</text>
    <text class="step-text" text-anchor="middle">
      <tspan x="646" y="371">Lorem ipsum dolor sit amet,</tspan>
      <tspan x="646" y="390">consectetur adipiscing elit,</tspan>
      <tspan x="646" y="409">sed do eiusmod tempor</tspan>
    </text>
  </g>

  <g class="step step--4">
    <circle class="step-circle--4" cx="842" cy="393" r="64"/>
    <text class="step-number" x="842" y="412" font-size="54" text-anchor="middle">04</text>
    <text class="step-text" text-anchor="middle">
      <tspan x="858" y="256">Lorem ipsum dolor sit amet,</tspan>
      <tspan x="858" y="275">consectetur adipiscing elit,</tspan>
      <tspan x="858" y="294">sed do eiusmod tempor</tspan>
    </text>
  </g>

  <g class="brand">
    <circle class="brand-dot" cx="140" cy="470" r="18"/>
    <text class="brand-name" x="140" y="533" text-anchor="middle">VORENTIX</text>
  </g>
</svg>
</body>
</html>
```